Build Website for Playful Brand that helps content creators build businesses

Please help me create a website for my company that helps content creators build businesses around their audience. I have attached a design and vibe that I am going for at mossquay.io.

Open for changes, but I want to keep the colour I currently have (a light teal). Ultimately the brand is playful but should come off as a very modern elevated brand.

I am looking for a few pages including

1. Home (with clear CTA button)
A section where I can input what the company does, and some brands that we have launched

2. About Me
A simple page, that has preferably able to put a circular image of myself and then give a quick background about the company

3. Blog (can you include how blog posts will appear and it should sit nicely in the page)
This ideally is a section that will be able to link to another software so my blogs automatically flow into here or posts. But otherwise it should have sections of blocks where creators can see about topics that I post about

4. Contact (this should include a form that will allow users to contact me)
Finally a contact page where it links my socials, similar what is there, but ideally there is a form they can fill out which I can link to my inbox as well. This should be a simple page as well

Create a multi page website, including a page that will link or can link blog post

Similar to this vibe and logo - https://mossquay.io/

Target Market(s)

Content Creators

Coding

Coded - Design and coding required

Number of Pages Required

4 page

Requirements
Must have
• Home, Contact Me (Including a place to submit an enquiry and form), Blog Post Page As well

```html
<!DOCTYPE html>
<html lang="en">
<head>
<meta charset="utf-8">
<title>Moss Quay — Empowering Entrepreneurs Through Content Creation</title>
<link href="https://fonts.googleapis.com/css2?family=Lato:wght@300;400;700;900&family=Arimo:wght@400;700&display=swap" rel="stylesheet">
<style>
:root{
  --teal:#5cb8aa;
  --teal-deep:#2f7a72;
  --teal-soft:#bff1ea;
  --teal-pale:#e6fbf8;
  --slate:#455a60;
  --slate-dark:#4a5c62;
  --ink:#1d1d1d;
  --muted:#8a8a8a;
  --grey-bg:#f2f2f2;
  --white:#ffffff;
}
*{box-sizing:border-box;margin:0;padding:0}
html,body{width:1200px;height:4566px;overflow:hidden}
body{position:relative;background:var(--white);font-family:"Arimo",Arial,sans-serif;color:var(--ink)}
.abs{position:absolute}
a{color:inherit;text-decoration:none}
.btn-dark{position:absolute;display:flex;align-items:center;justify-content:center;gap:8px;background:var(--slate);color:var(--white);border-radius:22px;font:700 12.5px "Arimo",Arial,sans-serif;letter-spacing:.3px}
.btn-dark .dot{width:11px;height:11px;border-radius:50%;background:var(--white);display:inline-flex;align-items:center;justify-content:center}
.btn-dark .dot::after{content:"";border-left:4px solid var(--slate);border-top:3px solid transparent;border-bottom:3px solid transparent;margin-left:1px}
.section-title{position:absolute;left:0;width:1200px;text-align:center;font:700 31px "Lato",sans-serif;color:var(--ink)}
.section-title .light{font-weight:300;color:#4d6a6a}
.brand-word{font:400 15px "Lato",sans-serif;letter-spacing:2px;color:var(--slate)}

/* header & hero */
.hero-bg{position:absolute;left:0;top:0;width:1200px;height:530px;background:linear-gradient(200deg,#c6f6ef 0%,#79cdbf 45%,#4fa99a 100%);clip-path:polygon(280px 0,1200px 0,1200px 530px,1090px 530px)}
.hero-wave{position:absolute;left:330px;top:170px;width:870px;height:210px}
.logo{position:absolute;left:142px;top:30px;width:150px;display:flex;flex-direction:column;align-items:center;gap:8px}
.logo .mark{width:34px;height:34px;border-radius:50%;background:var(--teal)}
.nav{position:absolute;top:33px;left:652px;display:flex;gap:34px;font:400 12.5px "Arimo",sans-serif;color:var(--white)}
.nav a.active{text-decoration:underline;text-underline-offset:4px}
.nav-cta{position:absolute;left:921px;top:23px;width:132px;height:39px;border-radius:20px;background:var(--white);color:var(--ink);font:700 12.5px "Arimo",sans-serif;display:flex;align-items:center;justify-content:center}
.hero-art{position:absolute;left:700px;top:90px;width:440px;height:430px;border-radius:16px;background:linear-gradient(160deg,#e8fbf8,#7cc9bc 60%,#3e9082)}
.eyebrow{position:absolute;left:142px;top:221px;font:700 13px "Arimo",sans-serif;display:flex;align-items:center;gap:10px}
.eyebrow::after{content:"";width:95px;height:1px;background:#9aa}
.hero-title{position:absolute;left:142px;top:260px;font:400 34px/1.4 "Lato",sans-serif;color:#3c5d5b}
.hero-title strong{display:block;font-weight:700;color:var(--ink)}

/* trusted */
.trusted{position:absolute;left:0;top:586px;width:1200px;text-align:center;font:700 23px "Lato",sans-serif}
.trusted span{font-weight:400;color:#3c5d5b}
.partners{position:absolute;left:150px;top:650px;width:900px;display:flex;justify-content:space-between;align-items:center}
.partner{width:62px;height:62px;border-radius:12px;background:#3f5e60;opacity:.85}
.partner.round{border-radius:50%}
.partner.wide{width:100px;height:40px;border-radius:8px}

/* about */
.about{position:absolute;left:0;top:796px;width:1200px;height:492px;background:var(--grey-bg)}
.about-art{position:absolute;left:168px;top:72px;width:355px;height:364px;border-radius:18px;background:linear-gradient(150deg,#d9f5f1,#5cb8aa 55%,#1f5d58)}
.about-portrait{position:absolute;left:370px;top:70px;width:120px;height:120px;border-radius:50%;background:linear-gradient(160deg,#a9b8bb,#44585d);border:5px solid var(--white)}
.about h2{position:absolute;left:649px;top:80px;font:700 31px "Lato",sans-serif}
.about h2 span{font-weight:300}
.about .rule{position:absolute;left:649px;top:128px;width:50px;height:1px;background:#999}
.about p{position:absolute;left:649px;width:370px;font:400 12.5px/24px "Arimo",sans-serif;color:var(--muted)}

/* offers */
.offer{position:absolute;width:292px;height:211px;background:var(--white);border-radius:6px;box-shadow:0 4px 16px rgba(0,0,0,.08);padding:26px 34px}
.offer.active{background:var(--teal-pale)}
.offer .icon{width:40px;height:34px;margin-bottom:12px}
.offer h3{font:700 14px "Arimo",sans-serif;margin-bottom:18px}
.offer p{font:400 12px/24px "Arimo",sans-serif;color:var(--muted)}
.pager{position:absolute;left:578px;top:1908px;display:flex;gap:4px}
.pager i{display:block;width:5px;height:5px;border-radius:3px;background:var(--teal)}
.pager i:first-child{width:24px}

/* why */
.why{position:absolute;left:0;top:1999px;width:1200px;height:487px;background:linear-gradient(115deg,#2f8a7d 0%,#6fc3b5 40%,#a9e9df 75%,#c5f4ee 100%)}
.why h2{position:absolute;left:0;width:1200px;top:78px;text-align:center;font:700 31px "Lato",sans-serif;color:var(--white)}
.why h2 span{font-weight:300}
.why .sub{position:absolute;left:0;width:1200px;top:148px;text-align:center;font:400 13.5px/23px "Arimo",sans-serif;color:#eaf8f6}
.stat{position:absolute;top:234px;width:183px;height:170px;background:var(--white);border-radius:22px;text-align:center;padding-top:64px}
.stat .badge{position:absolute;left:61px;top:-27px;width:60px;height:60px;border-radius:50%;background:var(--slate);border:4px solid var(--white);display:flex;align-items:center;justify-content:center;color:var(--white);font:400 16px "Arimo",sans-serif}
.stat b{display:block;font:700 14px "Arimo",sans-serif}
.stat small{display:block;font:400 13.5px "Arimo",sans-serif;color:var(--muted);margin-top:5px}
.stat strong{display:block;font:700 29px "Arimo",sans-serif;margin-top:14px}

/* faq */
.faq{position:absolute;width:372px;height:52px;border-bottom:1px solid #bdbdbd;font:400 15px/25px "Arimo",sans-serif}
.faq::after{content:"";position:absolute;right:6px;bottom:14px;width:5px;height:5px;border-right:1.5px solid #555;border-bottom:1.5px solid #555;transform:rotate(45deg)}

/* blog */
.blog-bg{position:absolute;left:0;top:2988px;width:1200px;height:459px;background:linear-gradient(180deg,#bff3ec,#8fdcd0 60%,#e4fbf8)}
.post{position:absolute;width:287px;height:366px;background:var(--white);border-radius:18px;box-shadow:0 6px 20px rgba(0,0,0,.1);padding:12px 12px 0}
.post.active{border:2px solid #7fd1c4}
.post .thumb{height:170px;border-radius:14px}
.post h3{margin:28px 16px 0;font:700 14px/23px "Arimo",sans-serif}
.post p{margin:10px 16px 0;font:400 12.5px/23px "Arimo",sans-serif;color:#555}
.post .more{margin:8px 16px 0;display:flex;align-items:center;gap:8px;font:700 12.5px "Arimo",sans-serif;color:var(--slate)}
.post .more i{width:11px;height:11px;border-radius:50%;background:var(--slate)}
.arrow{position:absolute;top:3253px;width:40px;height:40px;border-radius:50%;background:var(--white);box-shadow:0 2px 8px rgba(0,0,0,.12);display:flex;align-items:center;justify-content:center}

/* contact */
.form-panel{position:absolute;left:165px;top:3661px;width:399px;height:355px;background:#f1f1f3;border-radius:26px}
.field{position:absolute;left:39px;width:313px;height:43px;background:var(--white);border-radius:22px;padding:0 24px;font:400 10.5px/43px "Arimo",sans-serif;color:#555}
.field.area{height:111px;border-radius:24px;line-height:1;padding-top:22px}
.submit{position:absolute;left:287px;top:3996px;width:154px;height:37px;border-radius:20px;background:var(--slate);color:var(--white);font:700 12.5px/37px "Arimo",sans-serif;text-align:center}
.contact-art{position:absolute;left:656px;top:3668px;width:407px;height:381px;border-radius:28px;background:linear-gradient(160deg,#d7f7f2,#8ad9cc 55%,#1c2b2b)}

/* footer */
.footer{position:absolute;left:0;top:4111px;width:1200px;height:455px;background:var(--slate-dark);color:var(--white)}
.footer-logo{position:absolute;left:505px;top:-44px;width:190px;height:190px;border-radius:50%;background:var(--white);display:flex;flex-direction:column;align-items:center;justify-content:center;gap:10px;padding-top:30px}
.footer-logo .mark{width:32px;height:32px;border-radius:50%;background:var(--teal)}
.fcol{position:absolute;top:151px;font:400 12.5px/23px "Arimo",sans-serif;color:#e8eeee}
.fcol h4{font:700 13px "Arimo",sans-serif;color:var(--white);margin-bottom:14px;letter-spacing:.3px}
.newsletter{position:absolute;left:858px;top:4382px;width:204px;height:43px;border:2px solid var(--white);border-radius:22px;font:400 10px/39px "Arimo",sans-serif;padding-left:20px}
.newsletter span{position:absolute;right:3px;top:3px;width:33px;height:33px;border-radius:50%;background:var(--white)}
.socials{position:absolute;left:866px;top:4442px;display:flex;gap:10px}
.socials i{display:block;width:34px;height:34px;border-radius:50%;background:var(--white)}
.copyright{position:absolute;left:0;width:1200px;top:4528px;text-align:center;font:400 11px "Arimo",sans-serif;color:#e8eeee}
</style>
</head>
<body>

<!-- header / hero -->
<div class="hero-bg"></div>
<svg class="hero-wave" viewBox="0 0 870 210" fill="none" aria-hidden="true">
  <path d="M0 150 C200 40 380 220 560 110 S800 20 870 60" stroke="#ffffff" stroke-opacity=".5"/>
  <path d="M0 165 C210 60 390 230 570 125 S810 40 870 80" stroke="#9ddbd0" stroke-opacity=".7"/>
  <path d="M0 180 C220 80 400 240 580 140 S820 60 870 100" stroke="#cfcfcf" stroke-opacity=".6"/>
</svg>
<a class="logo" href="https://mossquay.io/"><span class="mark"></span><span class="brand-word">MOSS QUAY</span></a>
<nav class="nav">
  <a class="active" href="#">HOME</a><a href="#">ABOUT ME</a><a href="#">BLOG</a>
</nav>
<a class="nav-cta" href="#">CONTACT US</a>
<div class="hero-art" role="img" aria-label="Illustration of a creator working at a desk with an online sale on screen"></div>
<div class="eyebrow">WELCOME TO OUR COMPANY</div>
<h1 class="hero-title">Empowering Entrepreneurs<strong>Through Content Creation</strong></h1>
<a class="btn-dark" href="#" style="left:142px;top:392px;width:156px;height:39px">GET STARTED <span class="dot"></span></a>

<!-- trusted -->
<h2 class="trusted">Trusted by <span>3000+ Brands</span></h2>
<div class="partners" role="img" aria-label="Partner brand marks">
  <i class="partner round"></i><i class="partner"></i><i class="partner wide"></i><i class="partner"></i><i class="partner round"></i><i class="partner"></i><i class="partner round"></i>
</div>

<!-- about -->
<section class="about">
  <div class="about-art" role="img" aria-label="Illustration of a writer beside a large monitor showing a website"></div>
  <div class="about-portrait" role="img" aria-label="Circular portrait photo of the founder"></div>
  <h2>About <span>Me</span></h2>
  <div class="rule"></div>
  <p style="top:141px">Lorem ipsum dolor sit amet, consectetur adipiscing elit, sed do eiusmod tempor incididunt ut labore et dolore magna aliqua. Ut enim ad minim veniam, quis nostrud exercitation ullamco laboris nisi ut aliquip ex ea commodo consequat. Duis aute irure dolor in reprehenderit in voluptate velit esse cillum dolore eu fugiat nulla pariatur.</p>
  <p style="top:301px">Lorem ipsum dolor sit amet, consectetur adipiscing elit, sed do eiusmod tempor incididunt ut labore</p>
  <a class="btn-dark" href="#" style="left:649px;top:374px;width:154px;height:38px">LEARN MORE <span class="dot"></span></a>
</section>

<!-- offers -->
<h2 class="section-title" style="top:1367px">Content <span class="light">Moss Quay</span> Offers You</h2>
<div class="offer" style="left:144px;top:1442px">
  <svg class="icon" viewBox="0 0 40 34"><circle cx="26" cy="16" r="8" fill="none" stroke="#4a6a6a" stroke-width="2"/><path d="M32 22l6 6" stroke="#4a6a6a" stroke-width="2"/><rect x="2" y="10" width="14" height="12" rx="2" fill="#4a6a6a"/></svg>
  <h3>CONTENT SEO-OPTIMISED</h3><p>Lorem ipsum dolor sit amet, consectetur adipiscing elit, sed do eiusmod tempor incididunt ut labore et</p>
</div>
<div class="offer" style="left:454px;top:1442px">
  <svg class="icon" viewBox="0 0 40 34"><circle cx="18" cy="14" r="10" fill="none" stroke="#4a6a6a" stroke-width="2"/><circle cx="18" cy="14" r="4" fill="#5cb8aa"/><rect x="8" y="26" width="22" height="6" rx="2" fill="#4a6a6a"/></svg>
  <h3>HELP YOU GENERATE BUSINESS</h3><p>Lorem ipsum dolor sit amet, consectetur adipiscing elit, sed do eiusmod tempor incididunt ut labore et</p>
</div>
<div class="offer" style="left:764px;top:1442px">
  <svg class="icon" viewBox="0 0 40 34"><rect x="2" y="4" width="30" height="22" rx="2" fill="none" stroke="#4a6a6a" stroke-width="2"/><path d="M6 12h20M6 18h14" stroke="#5cb8aa" stroke-width="2"/><path d="M30 22l8-10" stroke="#4a6a6a" stroke-width="2"/></svg>
  <h3>FAST CONTENT DELIVERY</h3><p>Lorem ipsum dolor sit amet, consectetur adipiscing elit, sed do eiusmod tempor incididunt ut labore et</p>
</div>
<div class="offer" style="left:144px;top:1666px">
  <svg class="icon" viewBox="0 0 40 34"><rect x="2" y="4" width="20" height="16" rx="2" fill="none" stroke="#4a6a6a" stroke-width="2"/><circle cx="26" cy="22" r="7" fill="none" stroke="#5cb8aa" stroke-width="2"/><path d="M31 27l5 5" stroke="#4a6a6a" stroke-width="2"/></svg>
  <h3>GRAMMAR &amp; PLAGIARISM</h3><p>Lorem ipsum dolor sit amet, consectetur adipiscing elit, sed do eiusmod tempor incididunt ut labore et</p>
</div>
<div class="offer active" style="left:454px;top:1666px">
  <svg class="icon" viewBox="0 0 40 34"><rect x="6" y="2" width="22" height="30" rx="2" fill="none" stroke="#4a6a6a" stroke-width="2"/><path d="M10 10h14M10 16h14M10 22h8" stroke="#5cb8aa" stroke-width="2"/></svg>
  <h3>PREMIUM CONTENT</h3><p>Lorem ipsum dolor sit amet, consectetur adipiscing elit, sed do eiusmod tempor incididunt ut labore et</p>
</div>
<div class="offer" style="left:764px;top:1666px">
  <svg class="icon" viewBox="0 0 40 34"><circle cx="18" cy="16" r="12" fill="none" stroke="#4a6a6a" stroke-width="2"/><circle cx="18" cy="16" r="5" fill="#5cb8aa"/></svg>
  <h3>AWE-INSPIRING GRAPHICS</h3><p>Lorem ipsum dolor sit amet, consectetur adipiscing elit, sed do eiusmod tempor incididunt ut labore et</p>
</div>
<div class="pager"><i></i><i></i><i></i></div>

<!-- why -->
<section class="why">
  <h2>Why <span>Choose</span> Us</h2>
  <p class="sub">We offer impactful Content with 360o Approach that help your ventures<br>to grow 10x faster.</p>
  <div class="stat" style="left:184px"><span class="badge">Aa</span><b>Word Written</b><small>Till Date</small><strong>100 M+</strong></div>
  <div class="stat" style="left:400px"><span class="badge"><svg width="14" height="18" viewBox="0 0 14 18"><path d="M7 1a6 6 0 0 0-6 6c0 4 6 10 6 10s6-6 6-10a6 6 0 0 0-6-6z" fill="#fff"/><circle cx="7" cy="7" r="2" fill="#455a60"/></svg></span><b>Countries</b><small>We Catered</small><strong>15+</strong></div>
  <div class="stat" style="left:617px"><span class="badge"><svg width="16" height="16" viewBox="0 0 16 16"><path d="M2 14l2-6 8-7 3 3-7 8z" fill="#fff"/></svg></span><b>Content We</b><small>Delivered</small><strong>100 k+</strong></div>
  <div class="stat" style="left:831px"><span class="badge"><svg width="16" height="16" viewBox="0 0 16 16"><circle cx="8" cy="5" r="3.5" fill="#fff"/><path d="M1 15c0-4 3-6 7-6s7 2 7 6z" fill="#fff"/></svg></span><b>Clients</b><small>We catered</small><strong>3 k+</strong></div>
</section>

<!-- faq -->
<h2 class="section-title" style="top:2567px">Any <span class="light">FAQ's</span></h2>
<div class="faq" style="left:200px;top:2650px">Sed ut perspiciatis unde omnis iste natus error sit voluptatem accusantium ?</div>
<div class="faq" style="left:615px;top:2650px">Sed ut perspiciatis unde omnis iste natus error sit voluptatem accusantium ?</div>
<div class="faq" style="left:200px;top:2746px">Sed ut perspiciatis unde omnis iste natus error sit voluptatem accusantium ?</div>
<div class="faq" style="left:615px;top:2746px">Sed ut perspiciatis unde omnis iste natus error sit voluptatem accusantium ?</div>
<div class="faq" style="left:200px;top:2842px">Sed ut perspiciatis unde omnis iste natus error sit voluptatem accusantium ?</div>
<div class="faq" style="left:615px;top:2842px">Sed ut perspiciatis unde omnis iste natus error sit voluptatem accusantium ?</div>

<!-- blog -->
<div class="blog-bg"></div>
<h2 class="section-title" style="top:3055px">Our <span class="light">Blog</span></h2>
<article class="post" style="left:138px;top:3104px">
  <div class="thumb" role="img" aria-label="Illustration of a blogger working on a laptop" style="background:linear-gradient(150deg,#d8f7f2,#6fc6b8)"></div>
  <h3>Sed ut perspiciatis unde omnis iste natus error sit acc</h3>
  <p>Sed ut perspiciatis unde omnis iste natus error sit voluptatem accusantium</p>
  <a class="more" href="#">LEARN MORE <i></i></a>
</article>
<article class="post active" style="left:457px;top:3136px">
  <div class="thumb" role="img" aria-label="Illustration of a team around a large video screen" style="background:linear-gradient(150deg,#e2faf6,#7ed0c3)"></div>
  <h3>Sed ut perspiciatis unde omnis iste natus error sit acc</h3>
  <p>Sed ut perspiciatis unde omnis iste natus error sit voluptatem accusantium</p>
  <a class="more" href="#">LEARN MORE <i></i></a>
</article>
<article class="post" style="left:774px;top:3104px">
  <div class="thumb" role="img" aria-label="Illustration of quality content with books and a writer" style="background:linear-gradient(150deg,#eefcfa,#7cc9bc)"></div>
  <h3>Sed ut perspiciatis unde omnis iste natus error sit acc</h3>
  <p>Sed ut perspiciatis unde omnis iste natus error sit voluptatem accusantium</p>
  <a class="more" href="#">LEARN MORE <i></i></a>
</article>
<a class="arrow" href="#" style="left:69px" aria-label="Previous"><svg width="8" height="10"><path d="M6 1L2 5l4 4" stroke="#333" fill="none"/></svg></a>
<a class="arrow" href="#" style="left:1082px" aria-label="Next"><svg width="8" height="10"><path d="M2 1l4 4-4 4" stroke="#333" fill="none"/></svg></a>

<!-- contact -->
<h2 class="section-title" style="top:3593px">Contact <span class="light">With</span> Us</h2>
<form class="form-panel">
  <div class="field" style="top:12px">NAME</div>
  <div class="field" style="top:71px">EMAIL</div>
  <div class="field" style="top:133px">PLACE</div>
  <div class="field area" style="top:197px">MESSAGE</div>
</form>
<a class="submit" href="#">SUBMIT</a>
<div class="contact-art" role="img" aria-label="Illustration of a person working at a laptop surrounded by plants"></div>

<!-- footer -->
<footer class="footer">
  <a class="footer-logo" href="https://mossquay.io/"><span class="mark"></span><span class="brand-word">MOSS QUAY</span></a>
  <div class="fcol" style="left:147px"><h4>OFFICES</h4>ADDRESS :<br>atus error voluptatem,<br>accusantium doloremque,<br>laudantium, totam .<br><br>EMAIL :<br>info@mossquay.io</div>
  <div class="fcol" style="left:420px"><h4>SERVICES</h4>Article Writing<br>Blog Writing<br>Case Study Writing<br>Product Descriptions<br>SEO Writing<br>Ebook Writing<br>Proofreading<br>Newsletter Writing</div>
  <div class="fcol" style="left:650px"><h4>INDUSTRIES</h4>Agriculture<br>Health &amp; Beauty<br>Automotive<br>Sports &amp; Fitness<br>Realestate &amp;<br>Construction<br>Entertainment &amp; Gaming<br>Marketing &amp; Advertising</div>
  <div class="fcol" style="left:858px;width:220px"><h4>JOIN OUR NEWSLETTER</h4>If you're driven by curiosity and love research-based design arguments, the newsletter is for you.</div>
</footer>
<div class="newsletter">ENTER EMAIL<span></span></div>
<div class="socials" aria-label="Social profiles"><i></i><i></i><i></i></div>
<p class="copyright">COPYRIGHT@2024 - ALL RIGHTS RESERVED BY MOSS QUAY</p>

</body>
</html>
```